Trend Board/ Collage- Body Jewelry

Trend: Body Jewelry

Trend Boards/ Collages: digital banner that shows the influence of the trend
• Photo Size: 425 X 513 pixels
• JPEG
• Including: sourcing and/ or creating key elements (prints, typography, photos)
• We need to establish a collage of photos that is laid out nicely and shows the influence of this trend
• Put the trend name within the photo
• Please see the attached photos for your reference.

1. Feature the Trend Name
• Use a high fashion font that relates to the trend
• Could feature the trend name with a background pattern that relates to the trend

Target Market(s)

Female: t young adult

Industry/Entity Type

Digital

Font styles to use
Decorative
Script

Requirements
Must have
• - Feature the trend name "Body Jewelry" within the photo
• -Sourcing and/ or creating key elements (prints, typography, photos)
• - Collage of a few photos

```html
<!DOCTYPE html>
<html lang="en">
<head>
<meta charset="utf-8">
<title>Body Jewelry – Trend Board</title>
<link rel="stylesheet" href="https://fonts.googleapis.com/css2?family=Sacramento&display=swap">
<style>
  :root {
    --hot-pink: #e8186a;
    --wave-pink: #e9468f;
    --coral-red: #d8394a;
    --lime-green: #1dbf62;
    --sun-yellow: #e6d21c;
    --stripe-dark: #b8a20f;
    --tangerine: #f0642e;
    --stripe-orange: #c94a1e;
    --cream: #f4ecc8;
    --sand: #e3cf98;
    --ink: #1f1f1f;
    --white: #ffffff;
    --violet: #9b2fd1;
  }
  html, body {
    margin: 0;
    padding: 0;
    width: 994px;
    height: 1200px;
    overflow: hidden;
    background: var(--white);
  }
  .trend-board {
    display: block;
    width: 994px;
    height: 1200px;
  }
  .trend-title {
    font-family: "Sacramento", cursive;
    font-size: 78px;
    fill: var(--white);
    stroke: var(--ink);
    stroke-width: 2.4px;
    paint-order: stroke;
  }
  .photo-frame { fill: var(--cream); }
  .ring-dashed { fill: none; stroke: var(--white); stroke-width: 4; stroke-dasharray: 14 10; }
  .ring-solid { fill: none; stroke: var(--white); stroke-width: 3; }
</style>
</head>
<body>
<svg class="trend-board" viewBox="0 0 828 1000" xmlns="http://www.w3.org/2000/svg">
  <defs>
    <pattern id="stripes-yellow" width="6" height="6" patternUnits="userSpaceOnUse">
      <rect width="6" height="6" fill="var(--sun-yellow)"/>
      <rect width="1.6" height="6" fill="var(--stripe-dark)"/>
    </pattern>
    <pattern id="stripes-orange" width="6" height="6" patternUnits="userSpaceOnUse">
      <rect width="6" height="6" fill="var(--tangerine)"/>
      <rect width="1.6" height="6" fill="var(--stripe-orange)"/>
    </pattern>
  </defs>

  <!-- background bands -->
  <g class="backdrop">
    <rect width="828" height="400" fill="var(--hot-pink)"/>
    <rect y="190" width="828" height="210" fill="var(--coral-red)"/>
    <rect y="400" width="828" height="335" fill="var(--wave-pink)"/>
    <rect y="735" width="828" height="265" fill="url(#stripes-orange)"/>
    <polygon points="0,95 828,95 414,935" fill="url(#stripes-yellow)"/>
    <polygon points="45,0 783,0 414,800" fill="var(--hot-pink)"/>
    <polygon points="95,0 733,0 414,700" fill="var(--lime-green)"/>
  </g>

  <!-- triangular photos -->
  <g class="photo photo-hand-chain" role="img" aria-label="Photo: woman with blonde hair wearing a gold hand chain">
    <polygon class="photo-frame" points="30,160 305,160 180,455"/>
    <polygon points="45,170 290,170 180,432" fill="#c9b9a6"/>
  </g>
  <g class="photo photo-collar" role="img" aria-label="Photo: model wearing a gold chain collar over a pink top">
    <polygon class="photo-frame" points="530,160 805,160 660,455"/>
    <polygon points="545,170 790,170 660,432" fill="#b98c72"/>
  </g>
  <g class="photo photo-head-chain" role="img" aria-label="Photo: model in gold head chain and knuckle rings">
    <polygon class="photo-frame" points="228,440 602,440 414,808"/>
    <polygon points="245,450 585,450 414,785" fill="#a99e94"/>
  </g>
  <g class="photo photo-body-chain" role="img" aria-label="Photo: body chain layered over a white shirt and blazer">
    <polygon class="photo-frame" points="192,740 395,740 300,940"/>
    <polygon points="205,748 382,748 300,922" fill="#7f7f84"/>
  </g>
  <g class="photo photo-back-chain" role="img" aria-label="Photo: draped chains across an open back">
    <polygon class="photo-frame" points="435,740 635,740 540,940"/>
    <polygon points="448,748 622,748 540,922" fill="#b49a84"/>
  </g>

  <!-- circular photos -->
  <g class="photo photo-anklet" role="img" aria-label="Photo: barefoot sandal chains and stacked bangles">
    <circle class="ring-dashed" cx="130" cy="560" r="132"/>
    <circle class="photo-frame" cx="130" cy="560" r="118"/>
    <circle cx="130" cy="560" r="108" fill="#8e8a72"/>
  </g>
  <g class="photo photo-pearl-back" role="img" aria-label="Photo: pearl strands draped across a bare back">
    <circle class="ring-dashed" cx="700" cy="560" r="132"/>
    <circle class="photo-frame" cx="700" cy="560" r="118"/>
    <circle cx="700" cy="560" r="108" fill="#b08d72"/>
  </g>
  <g class="photo photo-foot-chain" role="img" aria-label="Photo: gold layered foot chains on sand">
    <circle class="ring-solid" cx="120" cy="875" r="132"/>
    <circle class="ring-solid" cx="120" cy="875" r="122"/>
    <circle class="photo-frame" cx="120" cy="875" r="112"/>
    <circle cx="120" cy="875" r="103" fill="#b69a7c"/>
  </g>
  <g class="photo photo-gem-anklet" role="img" aria-label="Photo: gemstone barefoot sandal chains">
    <circle class="ring-solid" cx="710" cy="875" r="132"/>
    <circle class="ring-solid" cx="710" cy="875" r="122"/>
    <circle class="photo-frame" cx="710" cy="875" r="112"/>
    <circle cx="710" cy="875" r="103" fill="#d3bfae"/>
  </g>

  <!-- title emblem, layered above the photos -->
  <g class="title-emblem">
    <polygon points="160,45 668,45 414,460" fill="none" stroke="var(--white)" stroke-width="4"/>
    <polygon points="185,60 643,60 414,432" fill="var(--cream)"/>
    <polygon points="210,78 618,78 414,412" fill="var(--sand)" stroke="var(--ink)" stroke-width="3"/>
    <polygon points="248,100 580,100 414,372" fill="none" stroke="var(--ink)" stroke-width="2.5" stroke-dasharray="12 8"/>
    <text class="trend-title" x="412" y="215" text-anchor="middle" transform="rotate(-4 412 200)">Body Jewelry</text>
    <path d="M250,228 C300,232 340,242 395,254 C345,250 300,250 262,244 Z" fill="var(--hot-pink)"/>
    <path d="M578,228 C528,232 488,242 433,254 C483,250 528,250 566,244 Z" fill="var(--hot-pink)"/>
    <path d="M414,262 l-9,-9 a5.5,5.5 0 0 1 9,-6 a5.5,5.5 0 0 1 9,6 z" fill="var(--violet)"/>
  </g>
</svg>
</body>
</html>
```